Dellow Coaching flyer (women local)

Strapline: Do you want a more fulfilling and meaningful life?
Make 2015 a year for positive change

Image of an attractive woman in contemplation:

• I’ve lost my identity and wondering what life is about.

• I want more intimacy in my relationship

• I hate my career and don’t know what’s right for me

Personal Development Coaching can help you:

Testimonials from our clients:

‘I have changed the way I approach my daily life in order to achieve more for myself’.

‘Coaching has helped me change the way I think, focusing more on positive rather than negative thoughts’.

‘Without coaching, I believe that my life would have remained stagnant’.

‘ I have made the leap to set up my own business and have increased my income three fold’.

‘Coaching has helped me to grow closer than ever to my husband’.

Any relevant image and image of myself (included)

Why Dellow?

• Certified Personal Development Coach

• Experience coaching individuals wanting to effect change

Maud is a specialist in coaching for:

• Building confidence

• Feeling motivated and getting out of a rut

• Enhancing relationships with partners or family

• Making changes in your career or business

Book your free consultation (this should stand out)

e: maud@dellowexample.co.uk t: 0712 580 4163 w: www.dellowexample.co.uk (include logo, but change ‘Dellow Consulting’ to ‘Dellow Coaching’)
f: www.facebook.com/dellowexample.co.uk t: @mbdellow

* Notes in brackets are only instructions and not to be included as part of the flyer.

Flyer is is A5

Please not this flyer can be double sided as I feel there will be too much text for one side. Could you use image of woman in contemplation on front but not too depressing.

```html
<!DOCTYPE html>
<html lang="en">
<head>
<meta charset="utf-8">
<title>Dellow Coaching Flyer</title>
<link href="https://fonts.googleapis.com/css2?family=Open+Sans:wght@400;600;700;800&display=swap" rel="stylesheet">
<style>
  :root {
    --page-bg: #e9eaec;
    --paper: #ffffff;
    --blue: #3b6cb4;
    --navy: #1e3c8c;
    --cyan: #3cb6d8;
    --sky: #8fd3ec;
    --grey-text: #6b6b6b;
    --orange: #f26b1d;
    --orange-light: #ffa24a;
    --photo-light: #f3f5f7;
    --photo-mid: #d6dce2;
    --photo-deep: #9aa4ae;
  }
  * { box-sizing: border-box; margin: 0; padding: 0; }
  html, body {
    width: 1200px; height: 754px; overflow: hidden;
    background: var(--page-bg);
    font-family: "Open Sans", Arial, sans-serif;
  }
  .flyer {
    position: absolute; left: 355px; top: 30px;
    width: 490px; height: 695px;
    background: var(--paper);
    overflow: hidden;
    box-shadow: 0 2px 10px rgba(0,0,0,.18);
  }
  .hero-photo {
    position: absolute; left: 190px; top: 0; width: 300px; height: 430px;
    background:
      linear-gradient(90deg, #ffffff 0%, rgba(255,255,255,0) 40%),
      radial-gradient(ellipse 60% 70% at 62% 70%, rgba(70,78,90,.35) 0%, rgba(70,78,90,0) 70%),
      linear-gradient(180deg, var(--photo-light) 0%, var(--photo-mid) 55%, var(--photo-deep) 100%);
  }
  .headline {
    position: absolute; left: 12px; top: 6px;
    font-weight: 700; line-height: 1.0; text-transform: uppercase;
  }
  .headline .line { display: block; font-size: 29px; color: var(--blue); letter-spacing: -.3px; }
  .headline .line-accent { font-size: 25px; color: var(--cyan); }
  .logo-box {
    position: absolute; left: 378px; top: 0; width: 98px; height: 95px;
    background: var(--paper);
    box-shadow: 0 1px 4px rgba(0,0,0,.2);
    text-align: center; color: var(--cyan);
    font-weight: 400; font-size: 14px; line-height: 1.2;
  }
  .logo-box .mark {
    display: block; width: 22px; height: 22px; border-radius: 50%;
    background: var(--cyan); margin: 14px auto 8px;
  }
  .year-line {
    position: absolute; left: 12px; top: 103px;
    font-size: 26px; line-height: 1.0; text-transform: uppercase; color: var(--navy);
  }
  .year-line .accent { color: var(--cyan); }
  .year-line strong { color: var(--blue); font-weight: 700; }
  .concerns {
    position: absolute; left: 14px; top: 214px; list-style: none;
    font-size: 14px; line-height: 1.15; color: var(--navy); text-transform: uppercase;
  }
  .concerns li { margin-bottom: 9px; }
  .wave-band { position: absolute; left: 0; top: 372px; width: 490px; height: 130px; }
  .offer-badge { position: absolute; left: 22px; top: 360px; width: 122px; height: 122px; }
  .offer-badge .badge-text {
    position: absolute; inset: 0; display: flex; flex-direction: column;
    justify-content: center; align-items: center; text-align: center;
    color: #fff; font-weight: 800; text-transform: uppercase; line-height: 1.05;
    font-family: Georgia, "Times New Roman", serif;
    text-shadow: 0 1px 2px rgba(120,40,0,.5);
  }
  .badge-text .small { font-size: 12px; }
  .badge-text .big { font-size: 20px; }
  .coaching-pitch {
    position: absolute; left: 190px; top: 399px; width: 290px;
    text-align: center; color: #fff; font-weight: 800; text-transform: uppercase;
    line-height: 1.05; text-shadow: 0 1px 3px rgba(0,40,90,.55);
  }
  .coaching-pitch .small { display: block; font-size: 17px; }
  .coaching-pitch .big { display: block; font-size: 24px; margin-top: 3px; }
  .testimonials-title {
    position: absolute; left: 37px; top: 486px;
    font-size: 15px; font-weight: 700; color: var(--navy);
  }
  .testimonials {
    position: absolute; left: 28px; top: 514px; width: 440px;
    display: grid; grid-template-columns: 192px 192px; column-gap: 40px; row-gap: 12px;
    font-size: 11px; line-height: 1.3; color: var(--grey-text); list-style: none;
  }
  .testimonials q { quotes: "\201C" "\201E"; }
  .testimonials q::before, .testimonials q::after { font-size: 16px; color: #8a8a8a; line-height: 0; }
  .divider {
    position: absolute; left: 12px; top: 617px; width: 466px; height: 1px; background: var(--sky);
  }
  .contact {
    position: absolute; left: 12px; top: 625px;
    font-size: 11px; line-height: 1.2; color: var(--navy); font-style: normal;
  }
  .footer-logo {
    position: absolute; left: 390px; top: 625px; width: 92px;
    text-align: center; color: var(--cyan); font-size: 11px; line-height: 1.2;
  }
  .footer-logo .mark {
    display: block; width: 16px; height: 16px; border-radius: 50%;
    background: var(--cyan); margin: 2px auto 5px;
  }
</style>
</head>
<body>
  <main class="flyer">
    <div class="hero-photo" role="img" aria-label="Photo of a businesswoman in a dark suit standing in a bright office"></div>

    <h1 class="headline">
      <span class="line">Do you want</span>
      <span class="line line-accent">A more fulfilling and</span>
      <span class="line">Meaningful life?</span>
    </h1>

    <div class="logo-box">
      <span class="mark"></span>
      DELLOW<br>COACHING
    </div>

    <p class="year-line">
      <span class="accent">Make <strong>2015</strong> a year</span><br>
      For positive<br>
      Change
    </p>

    <ul class="concerns">
      <li>I’ve lost my identity and<br>wondering what life is about</li>
      <li>I want more intimacy in my<br>relationship</li>
      <li>I hate my career and don’t<br>know what’s right for me</li>
    </ul>

    <svg class="wave-band" viewBox="0 0 490 130" preserveAspectRatio="none" aria-hidden="true">
      <defs>
        <linearGradient id="band-blue" x1="0" y1="0" x2="1" y2="0">
          <stop offset="0" stop-color="#2f63b8"/>
          <stop offset="1" stop-color="#3f9fd8"/>
        </linearGradient>
        <linearGradient id="band-cyan" x1="0" y1="0" x2="1" y2="0">
          <stop offset="0" stop-color="#56c3e6"/>
          <stop offset="1" stop-color="#2aa9d9"/>
        </linearGradient>
      </defs>
      <path d="M0 40 C120 10 260 20 490 30 L490 100 C330 95 160 120 0 125 Z" fill="url(#band-blue)"/>
      <path d="M0 55 C140 25 300 45 490 42 L490 98 C320 92 150 112 0 118 Z" fill="url(#band-cyan)"/>
      <path d="M0 90 C150 70 320 90 490 80 L490 96 C320 104 160 100 0 110 Z" fill="#a7def2" opacity=".8"/>
      <path d="M0 112 C160 96 330 100 490 94 L490 130 L0 130 Z" fill="#ffffff"/>
    </svg>

    <div class="offer-badge">
      <svg viewBox="0 0 120 120" width="122" height="122" aria-hidden="true">
        <defs>
          <radialGradient id="badge-fill" cx=".5" cy=".45" r=".6">
            <stop offset="0" stop-color="#ffa24a"/>
            <stop offset="1" stop-color="#f26b1d"/>
          </radialGradient>
        </defs>
        <polygon fill="url(#badge-fill)" stroke="#ffffff" stroke-width="2"
          points="120,60 110,69.9 115.4,83 102.4,88.4 102.4,102.4 88.4,102.4 83,115.4 69.9,110 60,120 50.1,110 37,115.4 31.6,102.4 17.6,102.4 17.6,88.4 4.6,83 10,69.9 0,60 10,50.1 4.6,37 17.6,31.6 17.6,17.6 31.6,17.6 37,4.6 50.1,10 60,0 69.9,10 83,4.6 88.4,17.6 102.4,17.6 102.4,31.6 115.4,37 110,50.1"/>
      </svg>
      <div class="badge-text">
        <span class="small">Book your</span>
        <span class="big">Free</span>
        <span class="small">Consultation</span>
      </div>
    </div>

    <p class="coaching-pitch">
      <span class="small">Personal<br>Development Coaching</span>
      <span class="big">Can help you!</span>
    </p>

    <h2 class="testimonials-title">Testimonials from our clients:</h2>
    <ul class="testimonials">
      <li><q>Coaching has helped me change the way I think, focusing more on positive rather than negative thoughts</q></li>
      <li><q>I have changed the way I approach my daily life in order to achieve more for myself</q></li>
      <li><q>Without coaching, I believe that my life would have remained stagnant</q></li>
      <li><q>Coaching has helped me to grow closer than ever to my husband</q></li>
    </ul>

    <div class="divider"></div>

    <address class="contact">
      Book your free consultation:<br>
      e: maud@dellowexample.co.uk<br>
      t: 0712 580 4163<br>
      w: www.dellowexample.co.uk
    </address>

    <div class="footer-logo">
      <span class="mark"></span>
      DELLOW<br>COACHING
    </div>
  </main>
</body>
</html>
```